Onboarding Carousel UI/UX design

We need a great UI/UX design for our onboarding carousel as attached in the PDF document. The chosen designers will be given our brand book with colors and styles to be used. The images must be focused on the content of each slide and be professional unique style (Do not use the childish cartoons we have used for placeholders)

Industry/Entity Type

Mortgage Brokerage

Number of Pages Required

5+ page

Font styles to use
Other font styles liked:
• Roboto

Requirements
Must have
• Great UI / UX design
Very relevant content of the images to match the slide
Nice to have
• Brand book

https://pv.lumorak.com/view/ed991dda-3474-4c3e-9747-882e21ba3df5-b8ca/?fullscreen

Image styles we like. Would need to be customized and made unique for us.

https://pinvarlo.com/shots/6300615-Torvane-Quillet-Illustration-Collaboration
https://meltridgestudio.co.za/software-client-style-frames
Should not have
• Do not use the childish images we have used as placeholders

```html
<!DOCTYPE html>
<html lang="en">
<head>
<meta charset="utf-8">
<title>Onboarding Carousel – Harbourline Brokers</title>
<link rel="stylesheet" href="https://fonts.googleapis.com/css2?family=Roboto:wght@400;500&display=swap">
<style>
  :root {
    --page-bg: #ffffff;
    --screen-bg: #e9eff7;
    --ink: #1b1d22;
    --accent-blue: #1565c0;
    --accent-magenta: #e0107a;
    --button-text: #ffffff;
    --art-sky: #cfe6f3;
    --art-cyan: #3fc6e6;
    --art-gold: #f0b43a;
    --art-navy: #1f3d6e;
    --art-red: #e8412c;
  }
  * { box-sizing: border-box; margin: 0; padding: 0; }
  html, body {
    width: 1200px; height: 809px; overflow: hidden;
    background: var(--page-bg);
    font-family: "Roboto", Arial, sans-serif;
    color: var(--ink);
  }
  .carousel { position: relative; width: 1200px; height: 809px; }
  .screen {
    position: absolute; top: 80px; width: 306px; height: 662px;
    background: var(--screen-bg);
    box-shadow: 0 6px 18px rgba(30, 50, 80, 0.12);
    text-align: center;
  }
  .screen--welcome { left: 73px; }
  .screen--account { left: 447px; }
  .screen--secure { left: 820px; }

  .screen__art {
    position: absolute; left: 24px; right: 24px; top: 80px; height: 165px;
    border-radius: 10px;
  }
  .screen--welcome .screen__art {
    background: linear-gradient(135deg, var(--art-sky), #d8eef2 55%, #f6e2a6);
  }
  .screen--account .screen__art {
    background: linear-gradient(160deg, var(--art-cyan), var(--art-sky) 60%, #f3d08a);
  }
  .screen--secure .screen__art {
    background: linear-gradient(150deg, #8fd0f3, var(--art-cyan) 45%, #f08a7a);
  }

  .screen__title {
    position: absolute; left: 12px; right: 12px; top: 283px;
    font-size: 15px; font-weight: 500; line-height: 25px;
    text-transform: uppercase; letter-spacing: 0.1px;
  }
  .screen__lead {
    position: absolute; left: 20px; right: 20px;
    font-size: 15px; line-height: 22px;
  }
  .screen__note {
    position: absolute; left: 20px; right: 20px;
    font-size: 11.5px; line-height: 18px;
  }
  .screen--welcome .screen__lead { top: 345px; }
  .screen--welcome .screen__note { top: 431px; }
  .screen--account .screen__lead { top: 347px; }
  .screen--account .screen__note { top: 419px; }
  .screen--secure .screen__lead { top: 341px; font-size: 13.5px; line-height: 22px; }
  .screen--secure .screen__note { top: 417px; }

  .pager {
    position: absolute; left: 0; right: 0; top: 502px;
    display: flex; justify-content: center; gap: 7px;
  }
  .pager__dot {
    width: 12px; height: 12px; border-radius: 50%;
    border: 1.3px solid var(--accent-blue);
  }
  .pager__dot--active { background: var(--accent-blue); }

  .next-button {
    position: absolute; right: 24px; top: 553px;
    width: 111px; height: 37px;
    background: var(--accent-magenta); color: var(--button-text);
    font-size: 15px; font-weight: 500; line-height: 37px;
    text-transform: uppercase;
  }
  .login-prompt {
    position: absolute; left: 24px; top: 561px;
    text-align: left; font-size: 11.5px; line-height: 16px;
  }
  .login-prompt__link { color: var(--accent-blue); text-decoration: none; }
</style>
</head>
<body>
<main class="carousel">

  <section class="screen screen--welcome">
    <div class="screen__art" role="img" aria-label="Illustration of a team reviewing growth charts beside stacks of coins"></div>
    <h2 class="screen__title">Welcome to Harbourline Brokers<br>Apply online</h2>
    <p class="screen__lead">You can apply online for your next mortgage credit in about 20 minutes.</p>
    <p class="screen__note">It’s easy, and we will guide you all the way.<br>See the five simple steps that you have to take!</p>
    <div class="pager" aria-label="Step 1 of 7">
      <span class="pager__dot pager__dot--active"></span><span class="pager__dot"></span><span class="pager__dot"></span><span class="pager__dot"></span><span class="pager__dot"></span><span class="pager__dot"></span><span class="pager__dot"></span>
    </div>
    <p class="login-prompt">Already have an account?<br><a class="login-prompt__link" href="#">Logon</a></p>
    <div class="next-button">Next</div>
  </section>

  <section class="screen screen--account">
    <div class="screen__art" role="img" aria-label="Illustration of people building a personal profile list on a large screen"></div>
    <h2 class="screen__title">#1 Create your personal<br>account</h2>
    <p class="screen__lead">You will need a valid email address to create your account</p>
    <p class="screen__note">We will send you a confirmation email, make sure you click the link to verify your email address.</p>
    <div class="pager" aria-label="Step 2 of 7">
      <span class="pager__dot"></span><span class="pager__dot pager__dot--active"></span><span class="pager__dot"></span><span class="pager__dot"></span><span class="pager__dot"></span><span class="pager__dot"></span><span class="pager__dot"></span>
    </div>
    <div class="next-button">Next</div>
  </section>

  <section class="screen screen--secure">
    <div class="screen__art" role="img" aria-label="Illustration of a phone with a padlock, key and password field for account security"></div>
    <h2 class="screen__title">#2 Secure your account<br>with your mobile phone</h2>
    <p class="screen__lead">You will need a valid mobile phone number to enabletwo factor authentication.</p>
    <p class="screen__note">We will send you an SMS containing a security code to verify your mobile number.</p>
    <div class="pager" aria-label="Step 3 of 7">
      <span class="pager__dot"></span><span class="pager__dot"></span><span class="pager__dot pager__dot--active"></span><span class="pager__dot"></span><span class="pager__dot"></span><span class="pager__dot"></span><span class="pager__dot"></span>
    </div>
    <div class="next-button">Next</div>
  </section>

</main>
</body>
</html>
```